Zvo Klinieken website for a maxillofacial surgery clinic

It's a website for a clinic for maxillofacial surgery in WordPress . The website doesn't need to be complicated but has to look professional. It needs to be in Dutch so i can give the texts. Similar websites are www.tandartsenpraktijkveldorm.nl or www.pbtspecialisten.nl. Pages would be sort of similar to https://hetcentrumvoorgezichtszorg.nl/ or https://wervelmondclinics.nl/. Those lasts are maxillofacial surgery clinic websites, but there are little more extensive.
I uploaded the logo. If this is not the proper quality i can upload the eps. Logo was made through pixelforum.

Target Market(s)

Patients who can find me and see information about the clinic

Industry/Entity Type

Healthcare

Coding

Coded - Design and coding required

Number of Pages Required

5+ page

Font styles to use
Other font styles liked:
• Something standard professional

Colors
0054AA
0677BA
7BADD7
CADEEF
E8F1F8

Requirements
Nice to have
• Something in line with the logo. I prefer a little dark like the darker logos but I'm not sure if that's professional. Logos bkvzo and rlpw are instances i'm registered to so they will have to be on the website too but small somewhere.

```html
<!DOCTYPE html>
<html lang="nl">
<head>
<meta charset="utf-8">
<title>Zvo Klinieken – Kaakchirurgie</title>
<link rel="stylesheet" href="https://fonts.googleapis.com/css2?family=Ubuntu:wght@400;500;700&family=Open+Sans:wght@400;600;700&display=swap">
<style>
:root{
  --navy:#2f3c52;
  --navy-deep:#263246;
  --blue:#1e9be0;
  --blue-dark:#0677ba;
  --blue-soft:#7badd7;
  --blue-pale:#e8f1f8;
  --grey-bg:#f3f5f9;
  --text:#3a4556;
  --muted:#8b93a0;
  --line:#dde2ea;
  --white:#ffffff;
  --star:#f07a2a;
}
*{box-sizing:border-box;margin:0;padding:0}
html,body{width:1200px;height:4726px;overflow:hidden}
body{position:relative;font-family:"Open Sans",Arial,sans-serif;color:var(--text);background:var(--white)}
.abs{position:absolute}
h1,h2,h3,h4{font-family:"Ubuntu",Arial,sans-serif;font-weight:500}
.ph{position:absolute}

/* header */
.topbar{left:385px;top:0;width:815px;height:33px;background:var(--navy);color:#fff;font-size:11px;font-weight:700;display:flex;align-items:center}
.topbar span{display:flex;align-items:center;gap:8px;height:100%;padding:0 20px;white-space:nowrap}
.topbar .appt{background:var(--blue);width:256px;justify-content:center;text-transform:uppercase;font-size:10px}
.logo{display:flex;align-items:center;gap:10px;font-family:"Ubuntu",sans-serif;font-weight:500;font-size:24px;color:var(--blue)}
.logo i{width:22px;height:22px;border-radius:50%;background:var(--blue);display:block}
.nav{top:60px;font-size:11px;color:#333;display:flex}
.nav a{position:absolute;color:#333;text-decoration:none;white-space:nowrap}
.btn-outline{border:1px solid #333;color:#333;font-size:10px;font-weight:700;display:flex;align-items:center;justify-content:center;letter-spacing:.5px;border-radius:3px}

/* hero */
.hero{left:0;top:101px;width:1200px;height:618px;background:linear-gradient(180deg,#3d4654 0%,#5d6775 45%,#434c59 100%)}
.hero .shade{position:absolute;inset:0;background:radial-gradient(ellipse at 55% 35%,rgba(120,135,150,.45),rgba(30,36,46,.55))}
.tag{background:var(--blue);color:#fff;font-size:11px;font-weight:700;display:flex;align-items:center;justify-content:center}
.hero h1{position:absolute;left:0;width:1200px;text-align:center;color:#fff;font-size:62px;line-height:73px;font-weight:500}
.hero .more{left:517px;width:164px;height:46px;border:1.5px solid #fff;color:#fff;font-size:11px;font-weight:700;display:flex;align-items:center;justify-content:center;border-radius:3px}

/* about */
.label{font-size:12px;color:var(--blue);text-decoration:underline;text-underline-offset:3px}
.about h2{font-size:40px;line-height:53px;color:var(--navy);font-weight:500}
.about h3{font-size:21px;color:var(--navy);font-weight:400}
.about p{font-size:12.5px;line-height:21.5px;color:var(--muted)}
.btn-blue{background:var(--blue);color:#fff;font-size:15px;font-family:"Ubuntu",sans-serif;display:flex;align-items:center;justify-content:center;gap:10px;border-radius:3px}

/* services */
.services{left:0;top:1318px;width:1200px;height:651px;background:var(--grey-bg)}
.sec-title{position:absolute;left:0;width:1200px;text-align:center;font-size:40px;color:var(--navy)}
.sec-label{position:absolute;left:0;width:1200px;text-align:center;font-size:12px;color:var(--blue);text-decoration:underline;text-underline-offset:3px}
.svc-img{width:325px;height:261px}
.svc-icon{width:92px;height:92px;border-radius:50%;background:var(--navy);border:4px solid var(--grey-bg);box-shadow:0 0 0 2px var(--blue-soft);display:flex;align-items:center;justify-content:center}
.svc-cap{width:273px;height:96px;background:#fff;display:flex;align-items:center;justify-content:center;font-family:"Ubuntu",sans-serif;font-size:19px;color:var(--navy);box-shadow:0 4px 12px rgba(0,0,0,.06)}

/* 24/7 */
.band{left:0;top:1969px;width:1200px;height:308px;background:linear-gradient(90deg,#2b3444,#4a5363 50%,#2e3747)}
.band h2{position:absolute;left:0;width:1200px;top:110px;text-align:center;color:#fff;font-size:35px;line-height:43px;font-weight:400}
.band h2 em{font-style:normal;color:var(--blue)}
.pill{left:350px;top:2246px;width:501px;height:55px;background:#fff;border-radius:3px 3px 0 0;display:flex;align-items:center;justify-content:space-around;font-size:16px;color:#222;padding:0 20px;white-space:nowrap}

/* why */
.why{left:0;top:2277px;width:1200px;height:791px;background:linear-gradient(90deg,#f2f3f5 0%,#e9ebee 55%,#c9ccd1 100%)}
.why-photo{left:780px;top:2277px;width:420px;height:791px;background:linear-gradient(180deg,#a7adb6,#d4c3b6 40%,#bfc4cb)}
.feat{width:235px;height:263px;background:#fff;text-align:center;padding-top:34px;box-shadow:0 3px 12px rgba(0,0,0,.05)}
.feat .ic{width:84px;height:84px;border-radius:50%;background:var(--blue-pale);margin:0 auto;display:flex;align-items:center;justify-content:center}
.feat h4{font-size:21px;color:var(--navy);margin-top:26px}
.feat p{font-size:12.5px;line-height:19px;color:var(--muted);margin:16px 20px 0}
.feat.active{background:var(--navy)}
.feat.active h4,.feat.active p{color:#fff}
.feat.active .ic{background:#fff}

/* testimonials */
.testi-band{left:0;top:3068px;width:1200px;height:356px;background:linear-gradient(180deg,#323c4c,#262f3d)}
.tcard{width:301px;height:326px;background:#fff;box-shadow:0 6px 20px rgba(0,0,0,.08);padding:44px 40px 0 42px}
.stars{color:var(--star);font-size:15px;letter-spacing:9px}
.tcard p{font-size:12.5px;line-height:19px;color:var(--muted);margin-top:14px;height:100px}
.tcard hr{border:0;border-top:1px solid var(--line);margin-top:18px}
.who{display:flex;align-items:center;gap:14px;margin-top:28px}
.who .av{width:56px;height:56px;border-radius:50%;background:linear-gradient(135deg,#e9d6c6,#c7a48a)}
.who b{display:block;font-family:"Ubuntu",sans-serif;font-size:15px;color:var(--navy);font-weight:500}
.who small{font-size:13px;color:var(--muted)}
.quote{width:56px;height:56px;border-radius:50%;background:var(--blue);display:flex;align-items:center;justify-content:center;color:#fff;font-family:"Ubuntu",sans-serif;font-size:34px;font-weight:700}

/* contact */
.form-card{left:138px;top:3868px;width:923px;height:457px;background:#fff;border-radius:14px;overflow:hidden;box-shadow:0 10px 30px rgba(0,0,0,.12)}
.form-photo{left:0;top:0;width:462px;height:457px;background:linear-gradient(160deg,#d9e1e7,#a9b7c3 55%,#3a5673)}
.field{position:absolute;border:1px solid #cfd5dd;font-size:11px;color:#777;padding:10px 8px;background:#fff}
.form-title{font-family:"Open Sans",sans-serif;font-size:27px;color:var(--text)}

/* footer */
.fnav{top:4488px;left:0;width:1200px;display:flex;justify-content:center;gap:48px;color:#fff;font-size:14px;font-weight:600}
.fline{left:140px;top:4538px;width:920px;height:1px;background:rgba(255,255,255,.25)}
.finfo{display:flex;align-items:center;gap:14px;color:#fff;font-size:11px;font-weight:700;line-height:16px;white-space:nowrap}
.finfo .c{width:54px;height:54px;border-radius:50%;border:1.5px solid rgba(255,255,255,.7);display:flex;align-items:center;justify-content:center;flex:none}
.fsep{width:1px;height:58px;background:rgba(255,255,255,.6)}
.bottombar{left:0;top:4668px;width:1200px;height:58px;background:var(--blue);color:#fff;font-size:12px;font-weight:700}
.soc{width:24px;height:24px;border:1.5px solid #fff;border-radius:3px}
</style>
</head>
<body>

<!-- header -->
<div class="abs topbar">
  <span style="width:210px;justify-content:center">
    <svg width="13" height="13" viewBox="0 0 24 24" fill="#fff"><path d="M6.6 10.8a15.1 15.1 0 0 0 6.6 6.6l2.2-2.2c.3-.3.7-.4 1-.2 1.1.4 2.3.6 3.6.6.6 0 1 .4 1 1V20c0 .6-.4 1-1 1A17 17 0 0 1 3 4c0-.6.4-1 1-1h3.5c.6 0 1 .4 1 1 0 1.3.2 2.5.6 3.6.1.3 0 .7-.2 1z"/></svg>
    020 - 418 - 5537</span>
  <span class="appt">
    <svg width="16" height="12" viewBox="0 0 24 18" fill="none" stroke="#fff" stroke-width="2"><rect x="1" y="1" width="22" height="16"/><path d="M1 1l11 9 11-9"/></svg>
    Request an appointment</span>
  <span style="font-size:10px">
    <svg width="12" height="14" viewBox="0 0 24 28" fill="#fff"><path d="M12 0a10 10 0 0 0-10 10c0 7.5 10 18 10 18s10-10.5 10-18A10 10 0 0 0 12 0zm0 14a4 4 0 1 1 0-8 4 4 0 0 1 0 8z"/></svg>
    18 Lindenkade Rotterdam</span>
</div>
<div class="abs logo" style="left:189px;top:38px"><i></i>Zvo Klinieken</div>
<nav class="abs nav" style="left:0;width:1200px">
  <a style="left:398px">THUIS</a>
  <a style="left:472px">Behandelingenvergoeding</a>
  <a style="left:622px">Ons team</a>
  <a style="left:708px">Folders</a>
</nav>
<div class="abs btn-outline" style="left:932px;top:53px;width:118px;height:31px">CONTACT US</div>

<!-- hero -->
<section class="abs hero" role="img" aria-label="Kaakchirurg met mondkapje behandelt een oudere patiënt in de behandelstoel">
  <div class="shade"></div>
  <div class="abs tag" style="left:523px;top:202px;width:147px;height:31px">KAAKCHIRURGIE</div>
  <h1 style="top:244px">Symmetrie Vormgeven,<br>Harmonie Herstellen</h1>
  <div class="abs more" style="top:416px">MEER LEREN</div>
</section>

<!-- about -->
<div class="ph" role="img" aria-label="Lachend meisje bij de tandarts" style="left:90px;top:857px;width:248px;height:363px;background:linear-gradient(150deg,#9ec4d8,#d9b89e 55%,#c98a8a)"></div>
<div class="ph" role="img" aria-label="Arts in witte jas met tablet" style="left:350px;top:811px;width:226px;height:222px;background:linear-gradient(160deg,#f2f4f6,#dfe4ea 60%,#c9b3a3)"></div>
<div class="ph" role="img" aria-label="Glimlachende patiënte in de behandelstoel" style="left:350px;top:1046px;width:226px;height:220px;background:linear-gradient(160deg,#7fa6bd,#d99a4a 60%,#c9842f)"></div>
<div class="abs" style="left:297px;top:988px;width:104px;height:104px;border-radius:50%;background:#fff;box-shadow:0 4px 14px rgba(0,0,0,.12)"></div>

<section class="about">
  <div class="abs label" style="left:624px;top:836px">KWALITEITSBORGING</div>
  <h2 class="abs" style="left:624px;top:870px">Harmonie in Vorm,<br>Precisie in Functie</h2>
  <h3 class="abs" style="left:624px;top:1001px">Zelfvertrouwen Boetseren, Levens Vormgeven</h3>
  <p class="abs" style="left:624px;top:1045px;width:505px">Lorem ipsum dolor sit amet, consectetur adipiscing elit, sed do eiusmod tempor incididunt ut labore et dolore magna aliqua. Ut enim ad minim veniam, quis nos trud exercitation ullamco laboris nisi ut aliquip ex ea commodo consequat. Duis aute irure dolor in reprehenderit in voluptate velit esse cillum dolore eu fugiat nulla pariatur. Excepteur sint occaecat cupidatat non proident, sunt in culpa qui officia deserunt mollit anim id est laborum.</p>
  <div class="abs btn-blue" style="left:624px;top:1204px;width:152px;height:46px">Meer Leren
    <svg width="16" height="12" viewBox="0 0 16 12" fill="none" stroke="#fff" stroke-width="2"><path d="M1 6h13M9 1l5 5-5 5"/></svg></div>
</section>

<!-- services -->
<section class="abs services">
  <div class="sec-label" style="top:78px">Onze Diensten</div>
  <h2 class="sec-title" style="top:116px">Onze Diensten</h2>
</section>
<div class="ph svc-img" role="img" aria-label="Team van tandartsen en assistentes rond een patiënte" style="left:90px;top:1596px;background:linear-gradient(160deg,#dfe6ec,#8fb3c8 50%,#5d86a3)"></div>
<div class="ph svc-img" role="img" aria-label="Kind in de behandelstoel tijdens een controle" style="left:440px;top:1596px;background:linear-gradient(160deg,#9cc4e0,#5e9cd0 50%,#c9a58b)"></div>
<div class="ph svc-img" role="img" aria-label="Zorgverlener in groen uniform in de kliniek" style="left:791px;top:1596px;background:linear-gradient(160deg,#e4e7ea,#b7c0c6 50%,#6f9a8a)"></div>

<div class="abs svc-icon" style="left:206px;top:1550px">
  <svg width="40" height="40" viewBox="0 0 40 40" fill="none" stroke="#fff" stroke-width="3" stroke-linecap="round"><path d="M20 4v6M20 30v6M4 20h6M30 20h6M8.7 8.7l4.2 4.2M27.1 27.1l4.2 4.2M8.7 31.3l4.2-4.2M27.1 12.9l4.2-4.2"/></svg></div>
<div class="abs svc-icon" style="left:556px;top:1550px">
  <svg width="40" height="40" viewBox="0 0 40 40" fill="none" stroke="#fff" stroke-width="2.6" stroke-linejoin="round"><path d="M17 30V13a3 3 0 0 1 6 0v9l7 2c2 .6 3 2 2.6 4l-1.6 8H18z"/><path d="M13 15a7 7 0 1 1 14 0"/></svg></div>
<div class="abs svc-icon" style="left:907px;top:1550px">
  <svg width="40" height="40" viewBox="0 0 40 40" fill="#fff"><path d="M20 3l4 6h-3v7h-2V9h-3zM20 37l-4-6h3v-7h2v7h3zM3 20l6-4v3h7v2H9v3zM37 20l-6 4v-3h-7v-2h7v-3z"/></svg></div>

<div class="abs svc-cap" style="left:116px;top:1811px">Kaakchirurgie</div>
<div class="abs svc-cap" style="left:466px;top:1811px">Slaapgeneeskunde</div>
<div class="abs svc-cap" style="left:817px;top:1811px">Plastische Chirurgie</div>

<!-- 24/7 band -->
<section class="abs band" role="img" aria-label="Glimlachend zorgteam van de kliniek op de achtergrond">
  <h2>Wij zijn <em>24/7</em> bereikbaar om snel te reageren op uw<br>tandheelkundige behoeften</h2>
</section>

<!-- why -->
<section class="abs why"></section>
<div class="ph why-photo" role="img" aria-label="Lachende vrouw met gekruiste armen in een lichte ruimte"></div>
<div class="sec-label" style="top:2336px;color:#8fb8da">WHY CHOOSE US</div>
<h2 class="sec-title" style="top:2374px;font-size:38px;width:1200px;left:-12px">Waarom Voor Ons Kiezen</h2>
<div class="abs pill"><span>+ (031) 645-208-117</span><span>[or]</span><span>info@zvoklinieken.nl</span></div>

<div class="abs feat" style="left:97px;top:2470px">
  <div class="ic"><svg width="38" height="38" viewBox="0 0 40 40" fill="none" stroke="#1e9be0" stroke-width="2.6"><path d="M8 18a12 12 0 0 1 24 0"/><rect x="6" y="18" width="28" height="10" rx="3"/><path d="M14 32h12"/></svg></div>
  <h4>Professioneel</h4><p>Lorem ipsum dolor sit amet, consectetur adipiscing elit, sed do eiusmod tem</p></div>
<div class="abs feat active" style="left:354px;top:2470px">
  <div class="ic"><svg width="42" height="42" viewBox="0 0 40 40" fill="none" stroke="#1e9be0" stroke-width="3"><circle cx="20" cy="20" r="16"/><circle cx="20" cy="20" r="8"/></svg></div>
  <h4>Klantgericht</h4><p>Lorem ipsum dolor sit amet, consectetur adipiscing elit, sed do eiusmod tem</p></div>
<div class="abs feat" style="left:609px;top:2470px">
  <div class="ic"><svg width="38" height="38" viewBox="0 0 40 40" fill="none" stroke="#1e9be0" stroke-width="2.6" stroke-linecap="round"><circle cx="20" cy="8" r="3"/><path d="M8 14l12 4 12-4M20 18v8l-7 9M20 26l7 9"/></svg></div>
  <h4>Bewezen Record</h4><p>Lorem ipsum dolor sit amet, consectetur adipiscing elit, sed do eiusmod tem</p></div>
<div class="abs feat" style="left:97px;top:2754px">
  <div class="ic"><svg width="38" height="38" viewBox="0 0 40 40" fill="none" stroke="#1e9be0" stroke-width="2.6" stroke-linecap="round"><circle cx="13" cy="13" r="4"/><path d="M5 28a8 8 0 0 1 16 0zM24 12h11M24 19h11M24 26h11"/></svg></div>
  <h4>Persoonlijke Aanpak</h4><p>Lorem ipsum dolor sit amet, consectetur adipiscing elit, sed do eiusmod tem</p></div>
<div class="abs feat" style="left:354px;top:2754px">
  <div class="ic"><svg width="38" height="38" viewBox="0 0 40 40" fill="#1e9be0"><rect x="6" y="26" width="5" height="8"/><rect x="14" y="20" width="5" height="14"/><rect x="22" y="14" width="5" height="20"/><rect x="30" y="8" width="5" height="26"/></svg></div>
  <h4>Kwaliteitsborging</h4><p>Lorem ipsum dolor sit amet, consectetur adipiscing elit, sed do eiusmod tem</p></div>
<div class="abs feat" style="left:609px;top:2754px">
  <div class="ic"><svg width="38" height="38" viewBox="0 0 40 40" fill="none" stroke="#1e9be0" stroke-width="2.6"><rect x="5" y="5" width="10" height="8"/><rect x="25" y="5" width="10" height="8"/><rect x="5" y="27" width="10" height="8"/><rect x="25" y="27" width="10" height="8"/><path d="M15 9h10M10 13v14M30 13v14M15 31h10"/></svg></div>
  <h4>Ervaring</h4><p>Lorem ipsum dolor sit amet, consectetur adipiscing elit, sed do eiusmod tem</p></div>

<!-- testimonials -->
<section class="abs testi-band" role="img" aria-label="Behandelkamer met lamp, gedimd op de achtergrond">
  <div class="abs" style="left:0;width:1200px;top:92px;text-align:center;color:#fff;font-size:12px;font-weight:600;text-decoration:underline;text-underline-offset:3px">GETUIGENISSEN</div>
  <h2 class="sec-title" style="top:130px;color:#fff">Wat Klanten Zeggen</h2>
</section>

<div class="abs tcard" style="left:110px;top:3307px"><div class="stars">★★★★★</div>
  <p>Lorem ipsum dolor sit amet, consectetur adipiscing elit, sed do eiusmod tempor incididunt ut labore et dolore magna aliqua. Ut enim ad minim veniam, q</p><hr>
  <div class="who"><div class="av"></div><div><b>Sanne de Wit</b><small>Brussels</small></div></div></div>
<div class="abs tcard" style="left:461px;top:3307px"><div class="stars">★★★★★</div>
  <p>Lorem ipsum dolor sit amet, consectetur adipiscing elit, sed do eiusmod tempor incididunt ut labore et dolore magna aliqua. Ut enim ad minim veniam, q</p><hr>
  <div class="who"><div class="av"></div><div><b>Sanne de Wit</b><small>Brussels</small></div></div></div>
<div class="abs tcard" style="left:806px;top:3307px"><div class="stars">★★★★★</div>
  <p>Lorem ipsum dolor sit amet, consectetur adipiscing elit, sed do eiusmod tempor incididunt ut labore et dolore magna aliqua. Ut enim ad minim veniam, q</p><hr>
  <div class="who"><div class="av"></div><div><b>Sanne de Wit</b><small>Brussels</small></div></div></div>
<div class="abs quote" style="left:82px;top:3341px">“</div>
<div class="abs quote" style="left:433px;top:3341px">“</div>
<div class="abs quote" style="left:778px;top:3341px">“</div>

<!-- footer background -->
<svg class="abs" style="left:0;top:4150px" width="1200" height="576" viewBox="0 0 1200 576">
  <path d="M0 90 C 300 140, 700 130, 1000 60 C 1080 40, 1150 20, 1200 0 V576 H0Z" fill="#2f3b4e"/>
  <path d="M1060 40 C 1120 60, 1170 100, 1200 150 V112 C 1170 80, 1120 40, 1080 20Z" fill="#1e9be0"/>
</svg>

<!-- contact -->
<div class="sec-label" style="top:3713px;left:-5px">CONTACT US</div>
<h2 class="sec-title" style="top:3752px;left:-5px">Kom Met Ons In Contact</h2>
<div class="abs form-card">
  <div class="ph form-photo" role="img" aria-label="Kaakchirurg in blauw uniform zittend in de behandelkamer"></div>
  <div class="abs form-title" style="left:512px;top:120px">Please fill out the form</div>
  <div class="field" style="left:512px;top:176px;width:359px;height:36px">Name</div>
  <div class="field" style="left:512px;top:229px;width:174px;height:36px">Phone</div>
  <div class="field" style="left:698px;top:229px;width:173px;height:36px">Email</div>
  <div class="field" style="left:512px;top:282px;width:359px;height:68px">Message</div>
  <div class="abs btn-blue" style="left:512px;top:368px;width:359px;height:38px;font-size:13px;font-family:'Open Sans',sans-serif;font-weight:600">Send</div>
</div>

<!-- footer -->
<div class="abs logo" style="left:0;width:1200px;justify-content:center;top:4386px;font-size:34px"><i style="width:28px;height:28px"></i>Zvo Klinieken</div>
<nav class="abs fnav"><span>HOME</span><span>SERVICES</span><span>ABOUT US</span><span>TESTIMONIALS</span><span>BLOG</span></nav>
<div class="abs fline"></div>

<div class="abs finfo" style="left:172px;top:4582px"><div class="c">
  <svg width="26" height="26" viewBox="0 0 24 24" fill="none" stroke="#fff" stroke-width="1.6"><circle cx="12" cy="12" r="10"/><path d="M2 12h20M12 2c3 3 3 17 0 20M12 2c-3 3-3 17 0 20"/></svg></div>
  <div>48, Medisch Centrum, Havenweg<br>Leiden, ZH 2312 AB</div></div>
<div class="abs fsep" style="left:430px;top:4580px"></div>
<div class="abs finfo" style="left:506px;top:4582px"><div class="c">
  <svg width="20" height="26" viewBox="0 0 16 24" fill="none" stroke="#fff" stroke-width="1.6"><rect x="2" y="1" width="12" height="22" rx="2"/><path d="M6 19h4"/></svg></div>
  <div>PHONE<br>(071) 582 3904</div></div>
<div class="abs fsep" style="left:750px;top:4580px"></div>
<div class="abs finfo" style="left:828px;top:4582px"><div class="c">
  <svg width="26" height="20" viewBox="0 0 24 18" fill="none" stroke="#fff" stroke-width="1.6"><rect x="1" y="1" width="22" height="16"/><path d="M1 1l11 9 11-9"/></svg></div>
  <div>EMAIL<br>contact@zvoklinieken.nl</div></div>

<div class="abs bottombar">
  <span class="abs" style="left:148px;top:20px">Zvo Klinieken</span>
  <div class="abs soc" style="left:934px;top:17px"></div>
  <div class="abs soc" style="left:966px;top:17px"></div>
  <div class="abs soc" style="left:998px;top:17px"></div>
  <div class="abs soc" style="left:1030px;top:17px"></div>
</div>

</body>
</html>
```